High-end construction company needs a business card design

We need a modern looking business card that draws people in, is memorable and looks so good people will want to sick it on their fridges.
On the first side what is needed are:
Logo
My name - Tomasz Brelwik
Title - Managing Director
Website - www.varkelt.co.uk
Email - tomasz@varkelt.co.uk
Telephone - 020 5194 6281
Mobile - 07845139072
On the back side was is needed is a list of all the services we provide:
-Kitchen Renovations
-Bathroom Renovations
-House Renovations
-Garage Conversions
-Extensions
-Loft Conversions
-Conservatories
-Carpentry
-Tiling
-Electrical
-Plumbing & Heating
-Bricklaying
-Landscaping
-Decorating
-Plastering
We would like the colours to be the same shades as on the logo with grey or black for the words.
Target Market(s)
Anyone who needs building work done
Contact Information for Business Card
This business card is for a construction company which strives to deliver excellent service and quality.
The look and feel of the card should represent this.
Requirements
Must have
- On the first side what is needed are:
Logo
My name - Tomasz Brelwik
Title - Managing Director
Website - www.varkelt.co.uk
Email - tomasz@varkelt.co.uk
Telephone - 020 5194 6281
Mobile - 07845139072
Nice to have
- Cool looking features

```html
<!DOCTYPE html>
<html lang="en">
<head>
<meta charset="utf-8">
<title>Varkelt Construction Ltd – Business Card</title>
<link rel="stylesheet" href="https://fonts.googleapis.com/css2?family=Lato:wght@400;700;900&display=swap">
<style>
  :root {
    --brand-green: #76c043;
    --text-grey: #555555;
    --paper: #ffffff;
  }
  html, body {
    margin: 0;
    padding: 0;
    overflow: hidden;
    background: var(--paper);
  }
  .card {
    position: relative;
    width: 1200px;
    height: 686px;
    background: var(--paper);
    font-family: "Lato", Arial, sans-serif;
    overflow: hidden;
  }
  .card-frame {
    position: absolute;
    left: 0;
    top: 0;
  }
  .brand {
    position: absolute;
    left: 389px;
    top: 190px;
    width: 457px;
    text-align: center;
    color: var(--brand-green);
    font-weight: 900;
    line-height: 1;
  }
  .brand-name {
    display: block;
    font-size: 96px;
    letter-spacing: 2px;
  }
  .brand-suffix {
    display: block;
    margin-top: 8px;
    font-size: 29px;
    letter-spacing: 6px;
  }
  .person {
    position: absolute;
    left: 242px;
    top: 407px;
    display: flex;
    align-items: center;
    gap: 30px;
  }
  .person-name {
    margin: 0;
    font-size: 55px;
    font-weight: 700;
    color: var(--text-grey);
  }
  .person-title {
    background: var(--brand-green);
    color: var(--paper);
    font-size: 28px;
    font-weight: 400;
    width: 341px;
    height: 57px;
    line-height: 57px;
    text-align: center;
  }
  .contact-list {
    position: absolute;
    left: 258px;
    top: 528px;
    margin: 0;
    padding: 0;
    list-style: none;
  }
  .contact-item {
    display: flex;
    align-items: center;
    height: 50px;
    margin-bottom: 4px;
    font-size: 29px;
    font-weight: 700;
    color: var(--text-grey);
  }
  .contact-icon {
    width: 32px;
    height: 32px;
    margin-right: 30px;
  }
  .phone-block {
    position: absolute;
    left: 644px;
    top: 534px;
    display: flex;
    align-items: center;
  }
  .phone-badge {
    width: 90px;
    height: 90px;
    margin-right: 25px;
  }
  .phone-numbers {
    margin: 0;
    padding: 0;
    list-style: none;
    font-size: 28px;
    font-weight: 700;
    color: var(--text-grey);
    line-height: 46px;
  }
</style>
</head>
<body>
<div class="card">
  <svg class="card-frame" width="1200" height="686" viewBox="0 0 1200 686" aria-hidden="true">
    <path d="M389 299 H27.5 V660.5 H1172.5 V299 H846" fill="none" stroke="var(--brand-green)" stroke-width="5"/>
  </svg>

  <div class="brand">
    <span class="brand-name">VARKELT</span>
    <span class="brand-suffix">CONSTRUCTION LTD</span>
  </div>

  <div class="person">
    <h1 class="person-name">Tomasz Brelwik</h1>
    <div class="person-title">Managing Director</div>
  </div>

  <ul class="contact-list">
    <li class="contact-item">
      <svg class="contact-icon" viewBox="0 0 32 32" aria-hidden="true">
        <rect x="3" y="4" width="26" height="18" rx="2" fill="var(--brand-green)"/>
        <circle cx="16" cy="13" r="5" fill="none" stroke="var(--paper)" stroke-width="1.6"/>
        <path d="M16 10.5 V13 H18" fill="none" stroke="var(--paper)" stroke-width="1.4"/>
        <rect x="13" y="22" width="6" height="4" fill="var(--brand-green)"/>
        <rect x="9" y="26" width="14" height="2.5" fill="var(--brand-green)"/>
      </svg>
      <span>www.varkelt.co.uk</span>
    </li>
    <li class="contact-item">
      <svg class="contact-icon" viewBox="0 0 32 32" aria-hidden="true">
        <rect x="3" y="8" width="26" height="17" fill="var(--brand-green)"/>
        <path d="M3 8 L16 18 L29 8" fill="none" stroke="var(--paper)" stroke-width="1.8"/>
      </svg>
      <span>tomasz@varkelt.co.uk</span>
    </li>
  </ul>

  <div class="phone-block">
    <svg class="phone-badge" viewBox="0 0 90 90" aria-hidden="true">
      <circle cx="45" cy="45" r="45" fill="var(--brand-green)"/>
      <path d="M31 24 c3-2 6-1 7 2 l4 8 c1 2 0 4-2 5 l-3 2 c2 6 7 11 13 13 l2-3 c1-2 3-3 5-2 l8 4 c3 1 4 4 2 7 l-3 4 c-2 2-5 3-8 2 C42 62 28 48 24 33 c-1-3 0-6 2-8 z" fill="var(--paper)"/>
    </svg>
    <ul class="phone-numbers">
      <li>020 5194 6281</li>
      <li>07845139072</li>
    </ul>
  </div>
</div>
</body>
</html>
```